FinTech company looking to revamp and expand client-facing interface for our financial models

Pellworth Engines currently has a very simple website that allows clients to interact with our financial models. We are looking to completely redesign the current site and add several extra pages to provide extra functionality. We want the design to have a modern, slick feel, that will work on both a desktop or a tablet. It should be straightforward for clients to move between different pages at any time, and clear from the layout how to interact with the more advanced features. We have included screenshots of existing pages in the attached design brief, as well as sketches of the functionality required by the new pages, but can't provide a direct link to the current site.
Target Market(s)
Professional investors that will be paying to access the interface
Industry/Entity Type
Finance
Number of Pages Required
4 page
Colors
Designer to choose colors to be used in the design.
Look and feel
Each slider illustrates characteristics of the customer's brand and the style your logo design should communicate.

```html
<!DOCTYPE html>
<html lang="en">
<head>
<meta charset="utf-8">
<title>QVANTA – Models</title>
<link href="https://fonts.googleapis.com/css2?family=Open+Sans:wght@400;600;700&display=swap" rel="stylesheet">
<style>
:root{
  --accent:#2bab95;
  --teal-dark:#006b66;
  --ink:#1a1a1a;
  --head-dark:#1c1c1c;
  --row-alt:#e3f3ee;
  --tab-white:#ffffff;
  --tab-grey:#e2e2e2;
  --tab-active:#cfcfcf;
  --band:#e6e6e6;
  --page:#f7f7f7;
  --line:#d6d6d6;
}
*{box-sizing:border-box;margin:0;padding:0}
html,body{width:1200px;height:678px;overflow:hidden}
body{font-family:"Open Sans",Arial,sans-serif;color:var(--ink);background:var(--page);position:relative}
.topbar{position:absolute;left:0;top:0;width:1200px;height:55px;background:#fff;box-shadow:0 3px 8px rgba(0,0,0,.12);z-index:3}
.brand{position:absolute;left:67px;top:0;line-height:55px;font-weight:700;font-size:18px;letter-spacing:.3px}
.nav-item{position:absolute;top:0;height:55px;display:flex;align-items:center;justify-content:center;gap:7px;font-weight:700;font-size:13px;border-right:1px solid #ececec}
.nav-item.active{background:var(--accent);color:#fff;border-right-color:var(--accent)}
.nav-item svg{width:22px;height:22px}
.band{position:absolute;left:0;top:55px;width:1200px;height:88px;background:linear-gradient(#f2f2f2,var(--band))}
.below{position:absolute;left:0;top:143px;width:1200px;height:535px;background:linear-gradient(#e4e4e4,var(--page) 140px)}
.tab{position:absolute;bottom:535px;width:143px;display:flex;align-items:center;justify-content:center;font-weight:600;font-size:12.5px;border-radius:4px 4px 0 0;background:var(--tab-white)}
.tab.low{height:32px}
.tab.high{height:41px}
.tab.equities{background:var(--tab-grey)}
.tab.current{background:var(--tab-active);height:51px}
.tab.icon{width:37px}
.export{position:absolute;left:1085px;top:183px;display:flex;align-items:center;gap:6px;color:var(--accent);font-weight:600;font-size:16px}
.models{position:absolute;left:97px;top:217px;width:1071px;border-collapse:collapse;table-layout:fixed;background:#fff;box-shadow:0 2px 8px rgba(0,0,0,.12);border-radius:6px;overflow:hidden;font-size:15.5px}
.models th{height:65px;color:#fff;font-weight:600;font-size:16px;background:var(--teal-dark);border-right:1px solid rgba(255,255,255,.25)}
.models th.meta{background:var(--head-dark);border-right-color:#444}
.models td{height:64.5px;padding:0 4px;border-right:1px solid #ececec;white-space:nowrap}
.models td.id{padding-left:17px}
.models td.sector,.models td.time{white-space:normal;line-height:22px}
.models td.sector{padding-left:17px}
.models td.time{text-align:center}
.models tbody tr:nth-child(even){background:var(--row-alt)}
.filters{position:absolute;left:0;top:235px;width:46px;height:176px;background:#d9d9d9;border-radius:0 5px 5px 0}
.filters span{position:absolute;left:23px;top:88px;transform:translate(-50%,-50%) rotate(-90deg);font-weight:700;font-size:14px;letter-spacing:.8px}
.filters svg{position:absolute;left:34px;top:311px}
</style>
</head>
<body>
<header class="topbar">
  <div class="brand">QVANTA</div>
  <div class="nav-item active" style="left:180px;width:83px">250D</div>
  <div class="nav-item" style="left:263px;width:83px">83D</div>
  <div class="nav-item" style="left:346px;width:83px">42D</div>
  <div class="nav-item active" style="left:554px;width:131px">
    <svg viewBox="0 0 24 24" fill="none" stroke="#fff" stroke-width="2"><path d="M3 11 12 3l9 8"/><path d="M5 10v10h5v-6h4v6h5V10"/></svg>MODELS</div>
  <div class="nav-item" style="left:685px;width:155px">
    <svg viewBox="0 0 24 24" fill="#222"><circle cx="12" cy="12" r="3"/><g><circle cx="12" cy="4" r="1.6"/><circle cx="12" cy="20" r="1.6"/><circle cx="4" cy="12" r="1.6"/><circle cx="20" cy="12" r="1.6"/><circle cx="6.3" cy="6.3" r="1.6"/><circle cx="17.7" cy="17.7" r="1.6"/><circle cx="6.3" cy="17.7" r="1.6"/><circle cx="17.7" cy="6.3" r="1.6"/></g></svg>SENSITIVITIES</div>
  <div class="nav-item" style="left:840px;width:157px">
    <svg viewBox="0 0 24 24" fill="none" stroke="#222" stroke-width="1.8"><circle cx="7" cy="7" r="4"/><circle cx="17" cy="7" r="4"/><circle cx="7" cy="17" r="4"/><circle cx="17" cy="17" r="4"/></svg>PORTFOLIO</div>
  <div class="nav-item" style="left:997px;width:138px">
    <svg viewBox="0 0 24 24" fill="none" stroke="#222" stroke-width="1.8"><rect x="2" y="4" width="20" height="16"/><path d="M5 16l4-5 3 3 4-6 3 4"/></svg>BACKTEST</div>
</header>

<div class="band"></div>
<div class="below"></div>

<nav>
  <div class="tab low equities" style="left:65px">EQUITIES</div>
  <div class="tab low" style="left:212px">ETFS</div>
  <div class="tab high" style="left:360px">PAIRS</div>
  <div class="tab current" style="left:508px">ETF PAIRS</div>
  <div class="tab high" style="left:655px">FACTORS</div>
  <div class="tab low" style="left:803px">NEW TAB TITLE #1</div>
  <div class="tab low" style="left:951px">NEW TAB TITLE #2</div>
  <div class="tab low icon" style="left:1098px"><svg width="14" height="18" viewBox="0 0 14 18"><path d="M3 2l7 7-7 7" fill="none" stroke="#888" stroke-width="3"/></svg></div>
  <div class="tab low icon" style="left:1140px"><svg width="22" height="22" viewBox="0 0 22 22" fill="none" stroke="#777" stroke-width="1.6"><circle cx="11" cy="11" r="9.5"/><path d="M11 6v10M6 11h10"/></svg></div>
</nav>

<div class="export">
  <svg width="24" height="22" viewBox="0 0 24 22" fill="none" stroke="#2bab95" stroke-width="2"><path d="M10 4H3v16h16v-7"/><path d="M8 15c1-6 6-9 13-9M16 2l5 4-5 4"/></svg>Export
</div>

<aside class="filters">
  <span>FILTERS</span>
</aside>
<svg style="position:absolute;left:34px;top:311px" width="26" height="26" viewBox="0 0 26 26"><circle cx="13" cy="13" r="12" fill="#0f2a4a" stroke="#fff" stroke-width="1.5"/><path d="M7 13h11M13 8l5 5-5 5" fill="none" stroke="#fff" stroke-width="2"/></svg>

<table class="models">
  <colgroup>
    <col style="width:92px"><col style="width:129px"><col style="width:106px"><col style="width:80px">
    <col style="width:83px"><col style="width:83px"><col style="width:83px"><col style="width:83px">
    <col style="width:83px"><col style="width:83px"><col style="width:83px"><col style="width:83px">
  </colgroup>
  <thead>
    <tr>
      <th class="meta">ID <svg width="10" height="8" viewBox="0 0 10 8"><path d="M1 2l4 4 4-4" fill="none" stroke="#fff" stroke-width="1.8"/></svg></th>
      <th class="meta">Sector</th><th class="meta">Time</th>
      <th>Quality</th><th>Stat 1</th><th>Stat 2</th><th>Stat 3</th><th>Stat 4</th><th>Stat 5</th><th>Stat 6</th><th>Stat 7</th><th>Stat 8</th>
    </tr>
  </thead>
  <tbody>
    <tr><td class="id">Model 1</td><td class="sector">Materials</td><td class="time">2019-07-03 12:15:00.000</td><td>30.2288</td><td>2.01574</td><td>23.305</td><td>-0.149368</td><td>22.3054</td><td>4.63714</td><td>0.945706</td><td>2.81949</td><td>2.60858</td></tr>
    <tr><td class="id">Model 2</td><td class="sector">Industrials</td><td class="time">2019-07-03 12:15:00.000</td><td>32.8694</td><td>0.87307</td><td>32.185</td><td>-0.033692</td><td>33.9911</td><td>11.5693</td><td>-0.472968</td><td>-0.830458</td><td>6.80646</td></tr>
    <tr><td class="id">Model 3</td><td class="sector">Consumer Discretionary</td><td class="time">2019-07-03 12:15:00.000</td><td>1.66002</td><td>-0.569222</td><td>159.814</td><td>0.0252328</td><td>172.616</td><td>10.2875</td><td>-0.750396</td><td>-0.385309</td><td>4.69146</td></tr>
    <tr><td class="id">Model 4</td><td class="sector">Information Technology</td><td class="time">2019-07-03 12:15:00.000</td><td>45.6856</td><td>0.412148</td><td>202.488</td><td>0.0084923</td><td>205.834</td><td>11.9094</td><td>-0.137913</td><td>0.449595</td><td>3.85106</td></tr>
    <tr><td class="id">Model 5</td><td class="sector">Information Technology</td><td class="time">2019-07-03 12:15:00.000</td><td>75.7733</td><td>7.06728</td><td>188.605</td><td>0.016913</td><td>161.665</td><td>3.82241</td><td>0.981019</td><td>1.29847</td><td>3.34927</td></tr>
  </tbody>
</table>
</body>
</html>
```